Need Flyer for Our Real estate Agency

Need to run General Campaign for our agency with Start of New Year as our theme ..Must have an agent's picture on the DL..
Address:
27 / 486Brindle rd, Marsden VIC 3047
Ph:03 9412 7306
email:info@kovalinrealestate.com.au
www.kovalinrealestate.com.au
Something like as attached picture..
Target Market(s)
Home Buyers
Industry/Entity Type
Real Estate Agent
Requirements
Must have
- Our Logo Colours

```html
<!DOCTYPE html>
<html lang="en">
<head>
<meta charset="utf-8">
<title>Kovalin Real Estate – DL Flyer</title>
<link rel="stylesheet" href="https://fonts.googleapis.com/css2?family=Lato:wght@300;400;700&family=Open+Sans:wght@400;700&display=swap">
<style>
  :root {
    --navy: #0f1f4e;
    --navy-deep: #0a1640;
    --navy-light: #1c3275;
    --maroon: #7a121c;
    --white: #ffffff;
    --canvas: #e3e3e3;
    --arc: #d4d6da;
    --photo-sky: #8aa4c4;
    --photo-house: #c9bfae;
    --photo-red: #c8433a;
    --photo-hand: #c79a80;
  }
  * { box-sizing: border-box; margin: 0; padding: 0; }
  html, body { width: 1181px; height: 1200px; overflow: hidden; }
  body { background: var(--canvas); font-family: "Lato", sans-serif; color: var(--white); position: relative; }

  .card { position: absolute; left: 60px; width: 1049px; height: 500px; overflow: hidden; box-shadow: 6px 8px 10px rgba(0,0,0,.28); }
  .card--front { top: 55px; }
  .card--back { top: 631px; }
  .card__shapes { position: absolute; inset: 0; }
  .abs { position: absolute; }

  .brand { display: flex; align-items: center; justify-content: center; gap: 12px; font-family: "Lato", sans-serif; font-weight: 400; letter-spacing: 5px; color: var(--white); }
  .brand__mark { width: 14px; height: 14px; background: var(--white); }
  .brand__name { font-size: 46px; }
  .front__brand { left: 80px; width: 420px; top: 120px; }
  .back__brand { left: 560px; width: 400px; top: 120px; }

  .headline { left: 60px; width: 460px; top: 230px; text-align: center; font-weight: 300; font-size: 36px; line-height: 49px; }
  .tagline { left: 20px; width: 560px; top: 352px; text-align: center; font-family: "Open Sans", sans-serif; font-size: 16.5px; text-transform: uppercase; }
  .tagline strong { font-weight: 700; }

  .cta { left: 90px; top: 404px; width: 396px; height: 50px; background: var(--white); border-radius: 25px; box-shadow: 0 3px 6px rgba(0,0,0,.35); display: flex; align-items: center; justify-content: center; gap: 8px; color: var(--maroon); font-family: "Open Sans", sans-serif; font-weight: 700; font-size: 21px; }
  .cta svg { width: 22px; height: 22px; }
  .cta__note { left: 60px; width: 460px; top: 462px; text-align: center; font-size: 18px; font-weight: 400; }

  .agent { left: 601px; top: 238px; font-size: 22px; font-weight: 400; }
  .contact { left: 601px; display: flex; align-items: center; gap: 12px; font-size: 18px; font-weight: 400; }
  .contact svg { width: 20px; height: 20px; flex: none; }
  .contact--phone { top: 286px; }
  .contact--email { top: 326px; }
  .contact--web { top: 364px; }
  .address { left: 520px; width: 500px; top: 449px; text-align: center; font-size: 19px; font-weight: 400; letter-spacing: .3px; }
</style>
</head>
<body>

<section class="card card--front">
  <svg class="card__shapes" viewBox="0 0 1049 500" width="1049" height="500">
    <defs>
      <linearGradient id="houseTones" x1="0" y1="0" x2="0" y2="1">
        <stop offset="0" stop-color="var(--photo-sky)"/>
        <stop offset=".55" stop-color="var(--photo-house)"/>
        <stop offset="1" stop-color="#4e6a3a"/>
      </linearGradient>
      <linearGradient id="navyFront" x1="0" y1="0" x2="1" y2="1">
        <stop offset="0" stop-color="var(--navy-light)"/>
        <stop offset="1" stop-color="var(--navy-deep)"/>
      </linearGradient>
    </defs>
    <rect x="560" y="0" width="489" height="500" fill="url(#houseTones)" role="img" aria-label="Agent in a navy suit standing before a lit two-storey family home"/>
    <path d="M0 0 H735 Q600 220 640 500 H0 Z" fill="var(--arc)"/>
    <path d="M0 0 H700 Q575 220 610 500 H0 Z" fill="url(#navyFront)"/>
    <path d="M700 0 Q575 220 610 500" fill="none" stroke="var(--white)" stroke-width="6"/>
    <path d="M0 428 H596 Q598 464 604 500 H0 Z" fill="var(--maroon)"/>
  </svg>

  <div class="abs brand front__brand"><span class="brand__mark"></span><span class="brand__name">KOVALIN</span></div>
  <p class="abs headline">Curios to know what your<br>home is worth?</p>
  <p class="abs tagline">Start of new year with <strong>Rohan Mehta</strong> and find out!</p>
  <div class="abs cta">
    <span>CALL ME NOW!</span>
    <svg viewBox="0 0 24 24"><circle cx="12" cy="12" r="10.5" fill="none" stroke="currentColor" stroke-width="2"/><path d="M8.2 6.8c.5-.5 1.2-.4 1.5.2l1 1.8c.3.5.1 1-.3 1.4l-.6.5c.6 1.3 1.5 2.3 2.8 3l.6-.6c.4-.4.9-.5 1.4-.2l1.7 1c.6.3.7 1 .2 1.5l-.8.8c-.8.8-2 .9-3.1.3-2.2-1.2-4-3-5.2-5.2-.6-1.1-.5-2.3.3-3.1z" fill="currentColor"/></svg>
    <span>0412 738 296</span>
  </div>
  <p class="abs cta__note">For Free property Appraisal</p>
</section>

<section class="card card--back">
  <svg class="card__shapes" viewBox="0 0 1049 500" width="1049" height="500">
    <defs>
      <linearGradient id="handTones" x1="0" y1="0" x2="1" y2="1">
        <stop offset="0" stop-color="#2a3a48"/>
        <stop offset=".45" stop-color="var(--photo-hand)"/>
        <stop offset=".7" stop-color="var(--photo-red)"/>
        <stop offset="1" stop-color="#33404d"/>
      </linearGradient>
      <linearGradient id="navyBack" x1="0" y1="0" x2="1" y2="1">
        <stop offset="0" stop-color="var(--navy-light)"/>
        <stop offset="1" stop-color="var(--navy-deep)"/>
      </linearGradient>
    </defs>
    <rect x="0" y="0" width="520" height="500" fill="url(#handTones)" role="img" aria-label="Hands sheltering a small red model house"/>
    <path d="M1049 0 H440 Q530 230 425 500 H1049 Z" fill="var(--arc)"/>
    <path d="M1049 0 H470 Q560 230 455 500 H1049 Z" fill="url(#navyBack)"/>
    <path d="M470 0 Q560 230 455 500" fill="none" stroke="var(--white)" stroke-width="6"/>
    <path d="M486 420 H1049 V500 H458 Q476 462 486 420 Z" fill="var(--white)"/>
    <path d="M490 428 H1049 V500 H462 Q479 466 490 428 Z" fill="var(--maroon)"/>
  </svg>

  <div class="abs brand back__brand"><span class="brand__mark"></span><span class="brand__name">KOVALIN</span></div>
  <p class="abs agent">Rohan Mehta, Director</p>
  <div class="abs contact contact--phone">
    <svg viewBox="0 0 24 24"><circle cx="12" cy="12" r="10.5" fill="none" stroke="var(--white)" stroke-width="1.6"/><path d="M8.2 6.8c.5-.5 1.2-.4 1.5.2l1 1.8c.3.5.1 1-.3 1.4l-.6.5c.6 1.3 1.5 2.3 2.8 3l.6-.6c.4-.4.9-.5 1.4-.2l1.7 1c.6.3.7 1 .2 1.5l-.8.8c-.8.8-2 .9-3.1.3-2.2-1.2-4-3-5.2-5.2-.6-1.1-.5-2.3.3-3.1z" fill="var(--white)"/></svg>
    <span>03 9412 7306</span>
  </div>
  <div class="abs contact contact--email">
    <svg viewBox="0 0 24 24"><circle cx="12" cy="12" r="10.5" fill="none" stroke="var(--white)" stroke-width="1.6"/><rect x="6.5" y="8" width="11" height="8" fill="none" stroke="var(--white)" stroke-width="1.5"/><path d="M6.5 8 L12 12.5 L17.5 8" fill="none" stroke="var(--white)" stroke-width="1.5"/></svg>
    <span>rohan.mehta@kovalinrealestate.com.au</span>
  </div>
  <div class="abs contact contact--web">
    <svg viewBox="0 0 24 24"><circle cx="12" cy="12" r="10.5" fill="none" stroke="var(--white)" stroke-width="1.6"/><circle cx="12" cy="12" r="6" fill="none" stroke="var(--white)" stroke-width="1.3"/><ellipse cx="12" cy="12" rx="2.6" ry="6" fill="none" stroke="var(--white)" stroke-width="1.2"/><path d="M6 12 H18" stroke="var(--white)" stroke-width="1.2"/></svg>
    <span>www.kovalinrealestate.com.au</span>
  </div>
  <p class="abs address">27/486 Brindle Rd Marsden, Victoria, Australia 3047</p>
</section>

</body>
</html>
```